Card Design for my dog training business Brightpaw Obedience

Need a business card design for my dog training business with my new logo. Want the card to come off professional yet fun. Want it to be very eye catchy as well. I normally have these at vet clinics, pet stores, and groomers. so need it to look better than my competitors.
Target Market(s)
dog owners
Industry/Entity Type
Dog Training
Contact Information for Business Card
needs logo, my name and info
Font styles to use
Serif
Colors
0255a3
ffffff
ec1f27
000000
333333
fbfbfb
Requirements
Must have
- Brightpaw Obedience
- Felix Orland
- 415 903 2276
- info@brightpawobedience.example
- www.brightpawobedience.example

```html
<!DOCTYPE html>
<html lang="en">
<head>
<meta charset="utf-8">
<title>Brightpaw Obedience – Business Card</title>
<link rel="stylesheet" href="https://fonts.googleapis.com/css2?family=Libre+Baskerville:ital,wght@0,400;0,700;1,400&display=swap">
<style>
  :root {
    --brand-blue: #0255a3;
    --accent-blue: #2a8fd8;
    --brand-red: #ec1f27;
    --card-black: #000000;
    --card-charcoal: #151515;
    --ink-white: #ffffff;
    --ink-soft: #fbfbfb;
    --stage: #333333;
  }
  * { margin: 0; padding: 0; box-sizing: border-box; }
  html, body {
    width: 800px;
    height: 1200px;
    overflow: hidden;
    background: var(--stage);
    font-family: "Libre Baskerville", Georgia, serif;
  }
  .canvas {
    width: 800px;
    height: 1200px;
    display: flex;
    flex-direction: column;
    align-items: center;
    justify-content: center;
    gap: 110px;
  }
  .card {
    position: relative;
    width: 640px;
    height: 366px;
    background: linear-gradient(160deg, var(--card-charcoal), var(--card-black));
    color: var(--ink-white);
  }

  /* Front */
  .card-front .brand {
    position: absolute;
    top: 110px;
    left: 0;
    right: 0;
    display: flex;
    align-items: center;
    justify-content: center;
    gap: 14px;
  }
  .brand-dot {
    width: 22px;
    height: 22px;
    border-radius: 50%;
    background: var(--ink-white);
  }
  .card-front .brand-name {
    font-size: 34px;
    font-weight: 400;
    color: var(--ink-white);
    letter-spacing: 1px;
  }
  .card-front .tagline {
    position: absolute;
    top: 232px;
    left: 0;
    right: 0;
    text-align: center;
    font-style: italic;
    font-size: 12px;
    color: var(--ink-soft);
    opacity: 0.85;
  }

  /* Back */
  .card-back .brand {
    position: absolute;
    top: 44px;
    left: 36px;
    display: flex;
    align-items: center;
    gap: 10px;
  }
  .card-back .brand-dot { background: var(--accent-blue); width: 16px; height: 16px; }
  .card-back .brand-name {
    font-size: 22px;
    color: var(--accent-blue);
  }
  .contact-list {
    position: absolute;
    top: 186px;
    left: 36px;
    list-style: none;
  }
  .contact-item {
    display: flex;
    align-items: center;
    gap: 10px;
    font-size: 11px;
    color: var(--ink-soft);
    height: 22px;
  }
  .contact-icon {
    width: 14px;
    height: 14px;
    flex: none;
  }
  .divider {
    position: absolute;
    top: 262px;
    left: 30px;
    right: 30px;
    height: 2px;
    background: var(--brand-red);
  }
  .person {
    position: absolute;
    top: 214px;
    right: 60px;
    text-align: left;
  }
  .person-name {
    font-size: 24px;
    color: var(--accent-blue);
    line-height: 1.2;
  }
  .person-role {
    margin-top: 18px;
    margin-left: 70px;
    font-size: 12px;
    color: var(--ink-soft);
  }
</style>
</head>
<body>
<main class="canvas">

  <section class="card card-front" aria-label="Card front">
    <div class="brand">
      <span class="brand-dot"></span>
      <span class="brand-name">Brightpaw Obedience</span>
    </div>
    <p class="tagline">“Training dogs across town, one dog at a time.”</p>
  </section>

  <section class="card card-back" aria-label="Card back">
    <div class="brand">
      <span class="brand-dot"></span>
      <span class="brand-name">Brightpaw Obedience</span>
    </div>

    <ul class="contact-list">
      <li class="contact-item">
        <svg class="contact-icon" viewBox="0 0 14 14" aria-hidden="true">
          <rect width="14" height="14" fill="var(--accent-blue)"/>
          <path d="M4 3 L6 3 L6.6 5.2 L5.5 6 Q6.5 8 8 8.5 L8.8 7.4 L11 8 L11 10 Q7 11 4.5 7.5 Q3.5 5.5 4 3Z" fill="#fff"/>
        </svg>
        <span>415 903 2276</span>
      </li>
      <li class="contact-item">
        <svg class="contact-icon" viewBox="0 0 14 14" aria-hidden="true">
          <rect width="14" height="14" fill="var(--accent-blue)"/>
          <rect x="3" y="4" width="8" height="6" fill="none" stroke="#fff" stroke-width="1"/>
          <path d="M3 4 L7 7.5 L11 4" fill="none" stroke="#fff" stroke-width="1"/>
        </svg>
        <span>info@brightpawobedience.example</span>
      </li>
      <li class="contact-item">
        <svg class="contact-icon" viewBox="0 0 14 14" aria-hidden="true">
          <rect width="14" height="14" fill="var(--accent-blue)"/>
          <circle cx="7" cy="7" r="4" fill="none" stroke="#fff" stroke-width="1"/>
          <ellipse cx="7" cy="7" rx="1.7" ry="4" fill="none" stroke="#fff" stroke-width="0.8"/>
          <line x1="3" y1="7" x2="11" y2="7" stroke="#fff" stroke-width="0.8"/>
        </svg>
        <span>www.brightpawobedience.example</span>
      </li>
    </ul>

    <div class="person">
      <p class="person-name">Felix Orland</p>
      <p class="person-role">Dog Trainer</p>
    </div>

    <div class="divider"></div>
  </section>

</main>
</body>
</html>
```